Website Design for my Copper Distillation Equipment Business Nature Sciencey Theme

I already have a website www.cascobrewworks.com and its a sitevelo website builder one. But I cannot get the design right at all. I need this fixed.

I have logo. I need a redesign, for my website, the home page, that maybe I can have something similar in design- I can use as template to copy, for other pages so the whole thing matches? Look at my website so you understand I have a few pages...but most are links. Its a competition. Code has to be easy for me to implement, I am not expert.

Your advice needed..It would be a plus if I can update this myself throughout time. If I could have this explained to me too, the maintenance of it...how would I do this too..etc..pretend I am a child when you explain, if you can. I am not good with this stuff but I am smart and can learn fast.

I want a high end look. Maybe like an ivy league college-y look too, real preppy, chemistry...science-y, nature like is good, leaves, drops water, fields of wheat, lavender, etc.

I want every page to look similar, but the home page is what I want to be the main showpiece,..and I want each page have a little text section, maybe a photos section and a video section, for that market. Like a nice website. If I am not doing this right, let me know. I can work with you. Just help me, please. Let me know if I am doing this right.

When I pick my winning design, for my website, I will hire the artist one-on-one to re-design my shopping cart next. Or if I need additional help with implementing this current design, I can hire the same artist again too. I have a blog that I may want to hire the redesign as well too, but later on. My point is I am not just looking for one project here but I want to follow up with winning artist. So it would be return business for the winner.

I got my logo done here so I am repeat customer. And I have given that winning artist other design work.

Target Market(s)

Moonshine Stills I sell most, Essential Oil Business, Micro and Craft Distilleries, Canna-businesses, Alcohol Fuel

Industry/Entity Type

Business

Number of Pages Required

5+ page

Colors
ec1f27

Requirements
Must have
• The categories for the stills must be prominent and eye catching. The main photo I would like to be naturelike theme, but you can try out different things with me. I am open to ideas and suggestions. I would like this to be implemented easy and fast.
Nice to have
• My logo in it. You can use any of my photos as well from my pictoshare account. https://www.pictoshare.com/photos/81724596@K09/
• Colors of my Logo...matching design.
• Maybe some basic stock photos you see would match for me..
• Chemistry like symbols for the categories, I love that.

```html
<!DOCTYPE html>
<html lang="en">
<head>
<meta charset="utf-8">
<title>Casco Distillers — Home</title>
<link rel="stylesheet" href="https://fonts.googleapis.com/css2?family=Open+Sans:wght@300;400;600&display=swap">
<style>
:root{
  --maroon:#3b0f10;
  --maroon-line:#5a2224;
  --title:#6b1c1c;
  --accent:#8a2323;
  --ink:#2a2a2a;
  --muted:#8c8c8c;
  --rule:#dedede;
  --footer-light:#f0f0f0;
  --footer-dark:#2b2b2b;
  --white:#ffffff;
}
*{box-sizing:border-box;margin:0;padding:0}
html,body{width:745px;height:1200px;overflow:hidden;background:var(--white)}
body{position:relative;font-family:"Open Sans",Arial,sans-serif;color:var(--ink)}
.abs{position:absolute}

/* header */
.brand{left:62px;top:11px;display:flex;align-items:center;gap:9px}
.brand-mark{width:45px;height:45px;border:3px solid var(--maroon);border-radius:50%}
.brand-name{font-size:22.5px;font-weight:400;color:var(--maroon);letter-spacing:.1px}
.call{right:62px;top:19px;display:flex;align-items:center;gap:5px;text-align:right}
.call small{display:block;font-size:7px;color:#666;line-height:9px}
.call strong{display:block;font-size:12.5px;font-weight:600;color:var(--ink);line-height:15px}
.call-icon{width:22px;height:22px;border:1px solid var(--rule);border-radius:50%;display:flex;align-items:center;justify-content:center}

/* nav */
.nav{left:0;top:74px;width:745px;height:28px;background:var(--maroon)}
.nav ul{list-style:none;display:flex;margin-left:61px;height:28px}
.nav li{font-size:7.5px;color:#e6d6d6;display:flex;align-items:center;justify-content:center;border-left:1px solid var(--maroon-line);height:28px}
.nav li:last-child{border-right:1px solid var(--maroon-line)}
.nav li.active{color:var(--white);font-weight:600}

/* hero */
.hero{left:0;top:102px;width:745px;height:274px;
  background:
    radial-gradient(ellipse 120px 90px at 385px 70px,#5f7a2a 0%,rgba(95,122,42,.6) 45%,rgba(95,122,42,0) 100%),
    radial-gradient(ellipse 70px 60px at 45px 150px,#b9c86a 0%,rgba(185,200,106,0) 100%),
    linear-gradient(180deg,#7d7566 0%,#8a8374 45%,#6e675a 100%)}
.hero-arrow{top:228px;width:16px;height:22px;background:rgba(0,0,0,.45);display:flex;align-items:center;justify-content:center}
.hero-caption{left:191px;top:338px;height:23px;padding:0 8px;background:rgba(35,35,35,.85);color:var(--white);font-size:11px;font-weight:600;display:flex;align-items:center;letter-spacing:.2px}

/* categories */
.categories{left:62px;top:404px;width:103px;height:278px;border:1px solid var(--rule);padding:3px 8px}
.categories li{list-style:none;font-size:7px;color:#444;height:24.5px;display:flex;align-items:center;border-bottom:1px solid var(--rule);padding-left:6px;position:relative}
.categories li:last-child{border-bottom:0}
.categories li::before{content:"";position:absolute;left:0;top:11px;width:2px;height:2px;background:#666;border-radius:50%}
.categories li.active{color:var(--accent)}

/* feature cards */
.card{top:404px;width:158px}
.card-photo{height:89px}
.card h3{margin-top:15px;font-size:9.3px;font-weight:600;color:var(--title);line-height:13px;text-transform:uppercase}
.card p{margin-top:7px;font-size:6.7px;line-height:11.7px;color:var(--muted);width:156px}
.btn{display:inline-flex;margin-top:8px;height:24px;padding:0 10px;border:1px solid var(--rule);font-size:6.5px;color:#555;align-items:center}

/* gallery */
.gallery{left:61px;top:712px;width:622px;height:135px;background:var(--maroon)}
.gallery h2{position:absolute;left:13px;top:11px;font-size:12.5px;font-weight:600;color:var(--white)}
.gallery-more{position:absolute;right:13px;top:13px}
.thumb{position:absolute;top:37px;width:142px;height:84px;border:2px solid #6e2a2b}

/* media */
.section-title{top:866px;font-size:12.5px;font-weight:600;color:var(--maroon)}
.video{left:62px;top:886px;width:301px;height:164px;
  background:linear-gradient(90deg,#5d5a4c 0%,#7c7766 40%,#6f6a55 70%,#8b8b80 100%)}
.play{left:193px;top:954px;width:37px;height:26px;background:#d4282a;border-radius:7px;display:flex;align-items:center;justify-content:center}
.shop{left:382px;top:886px;width:301px;height:165px;
  background:linear-gradient(180deg,#a4a39d 0%,#8e8c86 55%,#6a6963 100%)}
.shop-bar{left:382px;top:1005px;width:301px;height:46px;background:rgba(25,25,25,.85);color:var(--white);padding:8px 11px}
.shop-bar b{font-size:9.5px;font-weight:600}
.shop-bar span{font-size:6px}
.shop-bar p{font-size:5.8px;margin-top:4px}

/* footer */
.footer-info{left:0;top:1078px;width:745px;height:63px;background:var(--footer-light)}
.info{top:1094px;font-size:8.3px;color:#333;line-height:11.5px}
.info small{display:block;font-size:7.5px;color:#555}
.divider{left:530px;top:1093px;width:1px;height:34px;background:#d0d0d0}
.social{display:flex;gap:7px;margin-top:6px}
.social i{display:block;width:16px;height:16px;background:#7c8a9c;border-radius:2px}
.footer-bottom{left:0;top:1141px;width:745px;height:59px;background:var(--footer-dark);color:#bfbfbf;text-align:center}
.footer-bottom nav{margin-top:16px;font-size:7px}
.footer-bottom nav span{margin:0 5px;color:#666}
.footer-bottom p{margin-top:10px;font-size:6.8px}
</style>
</head>
<body>

<header>
  <div class="abs brand"><span class="brand-mark"></span><span class="brand-name">Casco Distillers</span></div>
  <div class="abs call">
    <div><small>Call us</small><strong>360-555-0142</strong></div>
    <span class="call-icon"><svg width="10" height="10" viewBox="0 0 24 24"><path d="M6.6 10.8a15 15 0 0 0 6.6 6.6l2.2-2.2c.3-.3.7-.4 1-.2 1.1.4 2.3.6 3.6.6.6 0 1 .4 1 1V20c0 .6-.4 1-1 1A17 17 0 0 1 3 4c0-.6.4-1 1-1h3.5c.6 0 1 .4 1 1 0 1.3.2 2.5.6 3.6.1.3 0 .7-.2 1z" fill="#888"/></svg></span>
  </div>
</header>

<nav class="abs nav">
  <ul>
    <li class="active" style="width:65px">HOME</li>
    <li style="width:78px">ABOUT US</li>
    <li style="width:60px">SHOP</li>
    <li style="width:68px">VIDEOS</li>
    <li style="width:70px">PHOTOS</li>
    <li style="width:68px">BOOKS</li>
    <li style="width:62px">BLOG</li>
    <li style="width:87px">CONTACT US</li>
    <li style="width:64px">LINKS</li>
  </ul>
</nav>

<section>
  <div class="abs hero" role="img" aria-label="Green herbal extract filtering through a paper filter in a wire funnel into a glass jar"></div>
  <div class="abs hero-arrow" style="left:0"><svg width="6" height="10"><path d="M5 1 1 5l4 4" stroke="#ddd" fill="none"/></svg></div>
  <div class="abs hero-arrow" style="right:0"><svg width="6" height="10"><path d="M1 1l4 4-4 4" stroke="#ddd" fill="none"/></svg></div>
  <div class="abs hero-caption">PURITY COMES FROM A DIRECT CONNECTION WITH NATURE...</div>
</section>

<ul class="abs categories">
  <li class="active">STILLS</li><li>ESSENTIAL OILS</li><li>ALCOHOL FUEL</li><li>CANNABIS</li><li>BOILERS</li><li>HOME DISTILLERS</li><li>VODKA STILL</li><li>HEAT CONTROL</li><li>DISTILLERY</li><li>KITS</li><li>PARTS</li>
</ul>

<article class="abs card" style="left:176px">
  <div class="card-photo" role="img" aria-label="Two polished copper stills against a grey block wall" style="background:linear-gradient(180deg,#a9a8a2 0%,#93918a 60%,#6f6d67 100%)"></div>
  <h3>Home distillers! We sell copper stills.</h3>
  <p>If you can boil water, you can distill. We sell a small 2 inch diameter 15 gallon moonshine still called, the "Tinsmith". Handcrafted and individually numbered. Our commitment to fine craftsmanship can be seen in every detail in each piece. We can do custom designs for each client as well. Our Copper Reflux towers can also double as a Pot Still. See the Stills page for more info.</p>
  <span class="btn">READ MORE</span>
</article>
<article class="abs card" style="left:350px">
  <div class="card-photo" role="img" aria-label="Large copper micro distillery still outdoors among trees" style="background:linear-gradient(180deg,#c9b34c 0%,#7d7a45 40%,#4a5a3a 75%,#3c4650 100%)"></div>
  <h3>Micro distillery equipment- copper stills for sale!</h3>
  <p>If you can boil water, you can distill. We sell a small 2 inch diameter 15 gallon moonshine still called, the "Tinsmith". Handcrafted and individually numbered. Our commitment to fine craftsmanship can be seen in every detail in each piece. We can do custom designs for each client as well. Our Copper Reflux towers can also double as a Pot Still. See the Stills page for more info.</p>
  <span class="btn">READ MORE</span>
</article>
<article class="abs card" style="left:524px">
  <div class="card-photo" role="img" aria-label="Person holding up a jar of golden herbal oil in front of a chalkboard" style="background:linear-gradient(90deg,#3d4a42 0%,#35466e 55%,#4a5a4c 100%)"></div>
  <h3>Sage herbal extractor- make cannabis oil with</h3>
  <p>If you can boil water, you can distill. We sell a small 2 inch diameter 15 gallon moonshine still called, the "Tinsmith". Handcrafted and individually numbered. Our commitment to fine craftsmanship can be seen in every detail in each piece. We can do custom designs for each client as well. Our Copper Reflux towers can also double as a Pot Still. See the Stills page for more info.</p>
  <span class="btn">READ MORE</span>
</article>

<section class="abs gallery">
  <h2>OUR GALLERY</h2>
  <svg class="gallery-more" width="11" height="11" viewBox="0 0 12 12"><circle cx="6" cy="6" r="5.2" stroke="#fff" fill="none"/><path d="M3.5 6h5M6.5 4l2 2-2 2" stroke="#fff" fill="none"/></svg>
  <div class="thumb" style="left:14px;background:linear-gradient(180deg,#2f3b4a,#4a5868)" role="img" aria-label="Painted sign for a small scale still supply"></div>
  <div class="thumb" style="left:166px;background:linear-gradient(90deg,#a48466,#7a5638)" role="img" aria-label="Pouring a sack of ingredient into a white bucket"></div>
  <div class="thumb" style="left:317px;background:linear-gradient(180deg,#a39482,#7a6a58)" role="img" aria-label="Hands arranging glassware and a stainless keg"></div>
  <div class="thumb" style="left:469px;background:linear-gradient(180deg,#7d8a8e,#5a6648)" role="img" aria-label="Copper still set up outdoors on a hillside"></div>
</section>

<h2 class="abs section-title" style="left:61px">OUR VIDEO</h2>
<h2 class="abs section-title" style="left:382px">OUR SHOP</h2>
<div class="abs video" role="img" aria-label="Video still of the distiller talking beside a ladder in a workshop"></div>
<div class="abs play"><svg width="10" height="11"><path d="M1 1l8 4.5L1 10z" fill="#fff"/></svg></div>
<div class="abs shop" role="img" aria-label="Two handmade copper stills for sale"></div>
<div class="abs shop-bar">
  <b>Copper Still for Sale!</b> <span>Also Moonshine Still Kits!</span>
  <p>Buy a Still today! Made by hand in the Pacific Northwest.</p>
  <svg class="abs" style="right:28px;top:14px" width="20" height="17" viewBox="0 0 24 20"><path d="M1 2h4l3 11h12l3-8H7" stroke="#fff" stroke-width="2.4" fill="none"/><circle cx="10" cy="17" r="2" fill="#fff"/><circle cx="18" cy="17" r="2" fill="#fff"/></svg>
</div>

<footer>
  <div class="abs footer-info"></div>
  <div class="abs info" style="left:78px"><small>Address</small>PO Box 2240 Elmhurst WA 98500 US</div>
  <div class="abs info" style="left:266px"><small>Phone</small>360-555-0142</div>
  <div class="abs info" style="left:383px"><small>E-mail</small>hello@cascodistillers.com</div>
  <div class="abs divider"></div>
  <div class="abs info" style="left:560px"><small>Follow us on :</small>
    <div class="social"><i aria-label="social link"></i><i aria-label="social link"></i><i aria-label="social link"></i><i aria-label="social link"></i>
      <svg width="16" height="16" viewBox="0 0 16 16"><rect x=".5" y="2.5" width="15" height="11" fill="#eee" stroke="#999"/><path d="M.5 2.5 8 9l7.5-6.5" stroke="#999" fill="none"/></svg>
    </div>
  </div>
  <div class="abs footer-bottom">
    <nav>Home<span>|</span>About us<span>|</span>Shop<span>|</span>Videos<span>|</span>Photos<span>|</span>Books<span>|</span>Blog<span>|</span>Contact us<span>|</span>Links</nav>
    <p>Copyright © 2015 Casco Distillers. All rights reserved</p>
  </div>
</footer>

</body>
</html>
```